Local Roofing/Construction company business needs new biz card design

We need a new business card design, current cards are from the start of this operation and generic at best. We are a local Construction Company (General Contractor) with a majority of our work originating from insurance claims-exterior finish work is the main focus (Roofs-Siding-Gutters etc). Heavily involved with homeowners and the low ball offers they receive from insurance company's after a insurable event takes place. I have attached some of our original logo file(s) below.

```html
<!DOCTYPE html>
<html lang="en">
<head>
<meta charset="utf-8">
<title>Stonefield Construction – Business Card</title>
<link href="https://fonts.googleapis.com/css2?family=Open+Sans:wght@400;600;700&display=swap" rel="stylesheet">
<style>
  :root {
    --canvas: #232323;
    --green: #52bd73;
    --green-light: #8fd6a4;
    --green-deep: #2f9a55;
    --ink: #061d21;
    --ink-soft: #0d2a2f;
    --white: #ffffff;
    --muted: #e6efee;
  }
  * { box-sizing: border-box; margin: 0; padding: 0; }
  html, body {
    width: 1200px; height: 780px; overflow: hidden;
    background: var(--canvas);
    font-family: "Open Sans", Arial, sans-serif;
  }
  .stage {
    position: relative; width: 1200px; height: 780px;
    display: flex; align-items: center; justify-content: center; gap: 40px;
  }
  .card {
    position: relative; width: 540px; height: 309px;
    border-radius: 3px; overflow: hidden;
    box-shadow: 0 10px 24px rgba(0,0,0,0.45);
  }

  /* Front */
  .card-front { background: var(--green); }
  .front-texture {
    position: absolute; inset: 0;
    background: linear-gradient(160deg, var(--green-light) 0%, var(--green) 45%, var(--green-deep) 100%);
  }
  .front-brand {
    position: absolute; right: 46px; bottom: 118px;
    display: flex; align-items: center; gap: 10px;
  }
  .brand-square { width: 18px; height: 18px; background: var(--ink); }
  .brand-name {
    font-weight: 700; font-size: 24px; letter-spacing: 1px;
    color: var(--ink); text-transform: uppercase;
  }

  /* Back */
  .card-back { background: var(--ink); }
  .back-wordmark {
    position: absolute; right: 28px; top: 14px; bottom: 14px; width: 92px;
    background: linear-gradient(180deg, #2e3b3d 0%, var(--ink-soft) 45%, var(--ink) 100%);
    border-radius: 14px;
    display: flex; align-items: center; justify-content: center;
  }
  .back-wordmark span {
    writing-mode: vertical-rl; transform: rotate(180deg);
    font-weight: 700; font-size: 40px; letter-spacing: 3px;
    color: #0f2f34; text-transform: uppercase;
  }
  .accent-bar {
    position: absolute; left: 40px; top: 132px; width: 12px; height: 50px;
    background: var(--green);
  }
  .contact { position: absolute; left: 62px; top: 126px; color: var(--white); }
  .person-name { font-size: 30px; font-weight: 700; line-height: 1.05; }
  .person-name .first { color: var(--green); }
  .person-title { font-size: 15px; font-weight: 600; margin-top: 2px; }
  .address { font-size: 13px; line-height: 1.3; margin: 12px 0 0 16px; }
  .lines { list-style: none; margin: 10px 0 0 16px; font-size: 13px; line-height: 1.35; }
  .lines li { display: flex; align-items: center; gap: 8px; }
  .lines svg { width: 12px; height: 12px; flex: none; }
</style>
</head>
<body>
<main class="stage">
  <section class="card card-front" aria-label="Card front">
    <div class="front-texture" role="img" aria-label="Repeating brand monogram pattern in shades of green"></div>
    <div class="front-brand">
      <span class="brand-square"></span>
      <span class="brand-name">Stonefield</span>
    </div>
  </section>

  <section class="card card-back" aria-label="Card back">
    <div class="back-wordmark"><span>Stonefield</span></div>
    <div class="accent-bar"></div>
    <div class="contact">
      <h1 class="person-name"><span class="first">Lena</span> Marchetti</h1>
      <p class="person-title">Managing Director</p>
      <p class="address">48 Cedar Hollow<br>Ln, Fairmont, MO 63012</p>
      <ul class="lines">
        <li>
          <svg viewBox="0 0 24 24"><path fill="#52bd73" d="M6.6 10.8a15 15 0 0 0 6.6 6.6l2.2-2.2a1 1 0 0 1 1-.25 11.4 11.4 0 0 0 3.6.57 1 1 0 0 1 1 1V20a1 1 0 0 1-1 1A17 17 0 0 1 3 4a1 1 0 0 1 1-1h3.5a1 1 0 0 1 1 1c0 1.25.2 2.45.57 3.6a1 1 0 0 1-.25 1z"/></svg>
          314-555-0142
        </li>
        <li>
          <svg viewBox="0 0 24 24"><path fill="#52bd73" d="M6.6 10.8a15 15 0 0 0 6.6 6.6l2.2-2.2a1 1 0 0 1 1-.25 11.4 11.4 0 0 0 3.6.57 1 1 0 0 1 1 1V20a1 1 0 0 1-1 1A17 17 0 0 1 3 4a1 1 0 0 1 1-1h3.5a1 1 0 0 1 1 1c0 1.25.2 2.45.57 3.6a1 1 0 0 1-.25 1z"/></svg>
          314-555-0187 (Emergency)
        </li>
        <li>
          <svg viewBox="0 0 24 24"><circle cx="12" cy="12" r="10" fill="none" stroke="#52bd73" stroke-width="2.4"/><path d="M2 12h20M12 2c3 3 3 17 0 20M12 2c-3 3-3 17 0 20" fill="none" stroke="#52bd73" stroke-width="2"/></svg>
          www.stonefieldbuild.com
        </li>
        <li>
          <svg viewBox="0 0 24 24"><rect x="2" y="5" width="20" height="14" rx="1.5" fill="none" stroke="#52bd73" stroke-width="2.4"/><path d="M3 6l9 7 9-7" fill="none" stroke="#52bd73" stroke-width="2.4"/></svg>
          office@stonefieldbuild.com
        </li>
      </ul>
    </div>
  </section>
</main>
</body>
</html>
```